Consulting business card

*1) An Overview:* The business is simply a financial transaction wherein I
offer to provide advice to financial holders of commercial real estate
mortgages (which are sub-performing or non-performing), and said holders
are desirous of selling said mortgages which I will offer advice to said
holders in the purchase of said mortgages. Please note the attached copy
of a proposed line-by-line business card which starts with the 1st line
"RKW Advisory, LLC" with the 2nd line "Purchase of Commercial Mortgage
Loan" and the 3rd line "Sub-performing and Non-performing" is my desired
copy subject to any suggested changes. Please ignore the the copy below
the aforementioned proposed card/copy as it will be activated at a later
date.and advise
*2) The Target Market:* I contact and advise senior officers in banks,
insurance companies, and financial institutions such as CEOs, CFOs, COOs,
and Loan Mitigation Officers: the senior officers are tasked with the
removal of sub-performing and non-performing commercial real estate loans
from their real estate portfolios. The desired market is targeted at $1-10
million USD and located in the US.
*3) Design Specifics: *STYLE should be conservative and be representative
of the financial market contacts; COLOR might show a rich forest green
element, a gold foil accent, and subtle black printing, however,
alternatively, silver foil accent(s) with strong black print would seem in
harmony with the services offered, however, I would appreciate any artful
suggestions; IMAGERY should be subtle (no logo can be strong enough to make
an immediate impact): the quality should make the recipient feel he/she has
just met an experienced and competent financial adviser (I have over 55
years of successful financial and business experience).
720.217.6154davidfredrickjones@gmail.com

```html
<!DOCTYPE html>
<html lang="en">
<head>
<meta charset="utf-8">
<title>RKW Advisory, LLC — Business Card</title>
<link rel="stylesheet" href="https://fonts.googleapis.com/css2?family=Tinos:wght@400;700&family=Arimo:wght@400;700&display=swap">
<style>
  :root {
    --backdrop: #e6e3de;
    --card-paper: #f6f4ef;
    --foil-gold: #b3a23a;
    --forest-green: #0f5a2a;
    --ink-black: #141414;
  }
  * { margin: 0; padding: 0; box-sizing: border-box; }
  html, body {
    width: 1200px;
    height: 857px;
    overflow: hidden;
    background: var(--backdrop);
  }
  .stage {
    width: 1200px;
    height: 857px;
    display: flex;
    align-items: center;
    justify-content: center;
  }
  .business-card {
    position: relative;
    width: 980px;
    height: 560px;
    padding: 12px;
    background: linear-gradient(to bottom, var(--foil-gold) 0%, var(--foil-gold) 45%, var(--forest-green) 45%, var(--forest-green) 100%);
    box-shadow: 0 10px 30px rgba(0,0,0,0.18);
  }
  .card-face {
    width: 100%;
    height: 100%;
    background: var(--card-paper);
    display: flex;
    flex-direction: column;
    align-items: center;
    text-align: center;
  }
  .company-name {
    margin-top: 58px;
    font-family: "Tinos", "Times New Roman", serif;
    font-weight: 700;
    font-size: 64px;
    line-height: 1;
    color: var(--foil-gold);
    letter-spacing: 0.5px;
  }
  .service-line {
    margin-top: 14px;
    font-family: "Arimo", Arial, sans-serif;
    font-weight: 700;
    font-size: 33px;
    line-height: 1.2;
    color: var(--ink-black);
  }
  .divider {
    margin-top: 26px;
    width: 820px;
    height: 2px;
    background: var(--ink-black);
  }
  .person-name {
    margin-top: 44px;
    font-family: "Tinos", "Times New Roman", serif;
    font-weight: 700;
    font-size: 52px;
    line-height: 1;
    color: var(--forest-green);
  }
  .contact-list {
    margin-top: 40px;
    font-family: "Arimo", Arial, sans-serif;
    font-weight: 400;
    font-size: 28px;
    line-height: 1.6;
    color: var(--ink-black);
  }
</style>
</head>
<body>
  <main class="stage">
    <article class="business-card">
      <div class="card-face">
        <h1 class="company-name">RKW Advisory, LLC</h1>
        <p class="service-line">Purchase of Commercial Mortgage Loan<br>Sub-performing and Non-performing</p>
        <div class="divider"></div>
        <h2 class="person-name">Daniel Marsh</h2>
        <p class="contact-list">555.304.8827<br>tomasheraldwick@mailbox.example</p>
      </div>
    </article>
  </main>
</body>
</html>
```